Marlow Dermal Studio - Business Banner with Brand Elements

Design:
• We would like to get a creative design for a wide banner that will go outside our medical spa clinic location. We need a designer to make a simple yet colorful and high-quality design layout. We want this banner to be eye-catching and to communicate the services we offer at our business: Laser Hair Removal | Veluxin | Lip Filler.

Requirements:
• We would like the banner to include our companies information which is the following:

Logo
“Refresh Your Skin”
Laser Hair Removal | Veluxin | Lip Filler
(520) 867-2291
www.MarlowDermalStudio.com

Colors:
• Our business colors are orange, a hint of black and white, but mostly peach/orange tones. (Orange: #f78f20 , White: #ffffff)

Fonts:
• Josefins Sans Bold & Lato

Content and images can be located here:
https://files.quibbleshare.com/share/folders/7tKwP3zRa9_LmQxVb2nD5yHc04EeJuFs8?mode=viewing

The following will give you an idea of our brand presentation:
• Our website is: www.MarlowDermalStudio.com
• Our Pictavo; @marlowdermalstudio
• Our Lumora: www.lumoranet.com/marlowdermalstudio

Target Market(s)
• Women 25 - 45

Industry/Entity Type
• Beauty

```html
<!DOCTYPE html>
<html lang="en">
<head>
<meta charset="utf-8">
<title>Marlow Dermal Studio – Banner Layouts</title>
<link rel="stylesheet" href="https://fonts.googleapis.com/css2?family=Josefin+Sans:ital,wght@0,400;0,600;0,700;1,300;1,400&display=swap">
<style>
  :root {
    --orange: #f37f1f;
    --white: #ffffff;
    --black: #141414;
    --board: #d9d9d9;
    --sky: #7ec6e6;
    --sea: #5ccbd6;
    --sand: #e9ddd0;
  }
  * { margin: 0; padding: 0; box-sizing: border-box; }
  html, body { width: 1200px; height: 847px; overflow: hidden; }
  body {
    background: var(--board);
    font-family: "Josefin Sans", sans-serif;
    position: relative;
  }
  .banner {
    position: absolute;
    left: 35px;
    width: 1130px;
    height: 388px;
    overflow: hidden;
    background: var(--orange);
  }
  .banner--light { top: 28px; }
  .banner--bold { top: 440px; }
  .banner__art { position: absolute; inset: 0; width: 100%; height: 100%; }
  .brand {
    position: absolute;
    display: flex;
    align-items: center;
    gap: 10px;
    font-weight: 700;
    font-size: 29px;
    letter-spacing: -0.3px;
    white-space: nowrap;
  }
  .brand__dot { width: 40px; height: 40px; border-radius: 50%; flex: none; }
  .tagline { position: absolute; font-weight: 700; white-space: nowrap; letter-spacing: 1px; }
  .services { position: absolute; font-style: italic; font-weight: 400; white-space: nowrap; letter-spacing: 1px; }
  .contact { position: absolute; font-weight: 600; white-space: nowrap; line-height: 1; }

  /* light banner */
  .banner--light .brand { right: 18px; top: 88px; color: var(--black); }
  .banner--light .brand__dot { background: var(--orange); }
  .banner--light .tagline { right: 18px; top: 178px; font-size: 25px; color: var(--black); }
  .banner--light .services { right: 18px; top: 219px; font-size: 19px; color: var(--black); }
  .banner--light .contact { left: 593px; color: var(--black); }
  .banner--light .contact--phone { top: 277px; font-size: 24px; letter-spacing: 1px; }
  .banner--light .contact--web { top: 336px; font-size: 22px; letter-spacing: 0.5px; }

  /* bold banner */
  .banner--bold .brand { left: 27px; top: 56px; color: var(--white); }
  .banner--bold .brand__dot { background: var(--white); }
  .banner--bold .services { left: 27px; top: 132px; font-size: 23px; color: var(--white); }
  .banner--bold .contact { left: 100px; color: var(--white); }
  .banner--bold .contact--phone { top: 198px; font-size: 24px; letter-spacing: 1px; }
  .banner--bold .contact--web { top: 266px; font-size: 23px; letter-spacing: 0.5px; }
  .banner--bold .tagline { left: 424px; top: 321px; font-size: 33px; color: var(--black); }
</style>
</head>
<body>

<section class="banner banner--light">
  <svg class="banner__art" viewBox="0 0 1600 550" preserveAspectRatio="none">
    <defs>
      <linearGradient id="beachLight" x1="0" y1="0" x2="0" y2="1">
        <stop offset="0" stop-color="#6fbfe2"/>
        <stop offset="0.5" stop-color="#a9d9e8"/>
        <stop offset="0.62" stop-color="#dfeff2"/>
        <stop offset="1" stop-color="#ece3d9"/>
      </linearGradient>
    </defs>
    <path role="img" aria-label="Photo: smiling woman in a straw hat on a sunny beach" fill="url(#beachLight)" d="M0 0 H590 C720 120 745 420 590 550 H0 Z"/>
    <path fill="#ffffff" d="M712 318 C900 185 1120 55 1600 70 V550 H615 C690 470 720 390 712 318 Z"/>
    <path fill="none" stroke="#ffffff" stroke-width="9" d="M712 304 C920 160 1140 30 1600 45"/>
    <path fill="#f37f1f" d="M1270 550 C1380 485 1490 440 1600 420 V550 Z"/>
    <path fill="none" stroke="#ffffff" stroke-width="4" d="M1255 550 C1370 475 1480 430 1600 408"/>
    <circle cx="772" cy="410" r="33" fill="#f37f1f"/>
    <path fill="#ffffff" d="M762 394 l7 -3 5 11 -5 4 c2 7 5 11 10 14 l5 -4 9 8 -3 7 c-12 2 -31 -20 -28 -37 z"/>
    <path fill="none" stroke="#ffffff" stroke-width="2" d="M777 396 a8 8 0 0 1 7 7 M778 389 a15 15 0 0 1 13 13"/>
    <circle cx="772" cy="490" r="33" fill="#f37f1f"/>
    <g fill="none" stroke="#ffffff" stroke-width="3">
      <circle cx="772" cy="490" r="16"/>
      <ellipse cx="772" cy="490" rx="7" ry="16"/>
      <path d="M756 490 H788 M759 482 H785 M759 498 H785"/>
    </g>
  </svg>
  <div class="brand"><span class="brand__dot"></span>Marlow Dermal Studio</div>
  <h2 class="tagline">Refresh Your Skin</h2>
  <p class="services">Laser Hair Removal | Veluxin | Lip Filler</p>
  <p class="contact contact--phone">(520) 867-2291</p>
  <p class="contact contact--web">www.MarlowDermalStudio.com</p>
</section>

<section class="banner banner--bold">
  <svg class="banner__art" viewBox="0 0 1600 550" preserveAspectRatio="none">
    <defs>
      <linearGradient id="beachBold" x1="0" y1="0" x2="0" y2="1">
        <stop offset="0" stop-color="#a7cde6"/>
        <stop offset="0.12" stop-color="#4fc6dc"/>
        <stop offset="0.45" stop-color="#8fd8dc"/>
        <stop offset="0.62" stop-color="#d9d6c9"/>
        <stop offset="1" stop-color="#efe3d6"/>
      </linearGradient>
    </defs>
    <path role="img" aria-label="Photo: smiling woman lying on the sand by turquoise sea" fill="url(#beachBold)" d="M380 550 C700 430 900 200 1120 110 C1300 40 1450 22 1600 28 V550 Z"/>
    <path fill="none" stroke="#141414" stroke-width="10" d="M395 545 C700 420 900 195 1120 105 C1300 35 1450 18 1600 22"/>
    <path fill="none" stroke="#ffffff" stroke-width="9" d="M430 515 C720 380 880 180 1100 92 C1290 18 1450 4 1600 8"/>
    <path fill="#ffffff" d="M0 495 C180 528 330 515 470 462 C340 528 160 550 0 550 Z"/>
    <path fill="none" stroke="#141414" stroke-width="3" d="M0 545 C170 545 340 525 470 462"/>
    <path fill="#f37f1f" d="M1170 550 C1350 470 1500 390 1600 318 V550 Z"/>
    <path fill="none" stroke="#ffffff" stroke-width="5" d="M1190 550 C1360 475 1505 395 1600 330"/>
    <circle cx="74" cy="298" r="32" fill="none" stroke="#ffffff" stroke-width="2"/>
    <path fill="#ffffff" d="M64 282 l7 -3 5 11 -5 4 c2 7 5 11 10 14 l5 -4 9 8 -3 7 c-12 2 -31 -20 -28 -37 z"/>
    <path fill="none" stroke="#ffffff" stroke-width="2" d="M79 284 a8 8 0 0 1 7 7 M80 277 a15 15 0 0 1 13 13"/>
    <circle cx="74" cy="394" r="32" fill="none" stroke="#ffffff" stroke-width="2"/>
    <g fill="none" stroke="#ffffff" stroke-width="3">
      <circle cx="74" cy="394" r="16"/>
      <ellipse cx="74" cy="394" rx="7" ry="16"/>
      <path d="M58 394 H90 M61 386 H87 M61 402 H87"/>
    </g>
  </svg>
  <div class="brand"><span class="brand__dot"></span>Marlow Dermal Studio</div>
  <p class="services">Laser Hair Removal | Veluxin | Lip Filler</p>
  <p class="contact contact--phone">(520) 867-2291</p>
  <p class="contact contact--web">www.MarlowDermalStudio.com</p>
  <h2 class="tagline">Refresh Your Skin</h2>
</section>

</body>
</html>
```